Create modern and sleek business card for luxury real estate company

We're a "boutique" real estate office looking for a design that gets across a highly modern luxury brand. Blacks and whites are probably the best colors unless we try a silver foil for the logo. I've attached a version of our current logo here. I'd like to swap out the current font on there with Gotham Light Regular.

I'm looking to have one side of the card have the logo with the space for our agents info on the other side.

Target Market(s)

Young professionals in a "luxury" headspace

Industry/Entity Type

Real estate

Contact Information for Business Card

A place for agent name, cell number, website. The slogan "Simply Rethinking Real Estate".

Font styles to use
Other font styles liked:
• Gotham Regular

Colors

Designer to choose only greyscale colors for use in the design.

Requirements
Must have
• Matte black as the background color. Clean lines and use of contrast. A specific design aspect that will use silver foil.
Nice to have
• Up in the air on integrating a QR code
Should not have
• Any houses or other real estate related design (ex: a clip art house)

```html
<!DOCTYPE html>
<html lang="en">
<head>
<meta charset="utf-8">
<title>Halden Realty — Business Card</title>
<link rel="stylesheet" href="https://fonts.googleapis.com/css2?family=Cormorant+Garamond:wght@600&family=Arimo:wght@400&display=swap">
<style>
  :root {
    --backdrop: #2b2b2b;
    --card: #0b0b0b;
    --card-edge: #050505;
    --ink: #f2f2f2;
    --ink-soft: #d9d9d9;
    --ghost: rgba(255,255,255,0.06);
  }
  * { margin: 0; padding: 0; box-sizing: border-box; }
  html, body { width: 1200px; height: 1015px; overflow: hidden; }
  body {
    background: var(--backdrop);
    display: flex;
    flex-direction: column;
    align-items: center;
    justify-content: center;
    gap: 60px;
  }
  .card {
    position: relative;
    width: 700px;
    height: 400px;
    background: radial-gradient(ellipse at 60% 40%, #1a1a1a 0%, var(--card) 70%, var(--card-edge) 100%);
    overflow: hidden;
    box-shadow: 0 18px 40px rgba(0,0,0,0.55);
  }
  .ghost-ring {
    position: absolute;
    width: 330px; height: 330px;
    border: 3px solid var(--ghost);
    border-radius: 50%;
    right: 40px; top: 35px;
  }
  .brand {
    position: absolute;
    display: flex;
    align-items: center;
    gap: 18px;
  }
  .brand-dot {
    width: 96px; height: 96px;
    border: 3px solid var(--ink);
    border-radius: 50%;
    flex: none;
  }
  .brand-name {
    font-family: "Cormorant Garamond", serif;
    font-weight: 600;
    color: var(--ink);
    font-size: 50px;
    line-height: 1;
    letter-spacing: 1px;
  }
  .brand-name .line1 {
    display: block;
    padding-bottom: 6px;
    border-bottom: 3px solid var(--ink);
    margin-bottom: 6px;
  }
  .brand-name .line2 { display: block; padding-left: 12px; }
  .card-front .brand { left: 170px; top: 140px; }
  .card-back .brand { left: 48px; top: 48px; }
  .agent {
    position: absolute;
    left: 175px;
    top: 190px;
    color: var(--ink);
    font-family: "Arimo", sans-serif;
  }
  .agent-name {
    font-family: "Cormorant Garamond", serif;
    font-weight: 600;
    font-size: 26px;
    letter-spacing: 1px;
    line-height: 1;
  }
  .agent-title { font-size: 17px; color: var(--ink-soft); margin-top: 2px; }
  .contact-list { list-style: none; margin-top: 18px; }
  .contact-list li {
    display: flex; align-items: center; gap: 8px;
    font-size: 17px; line-height: 24px;
  }
  .contact-list svg { width: 15px; height: 15px; flex: none; }
  .address { margin-top: 14px; font-size: 17px; line-height: 22px; }
</style>
</head>
<body>
  <section class="card card-front" aria-label="Card front">
    <div class="ghost-ring"></div>
    <div class="brand">
      <div class="brand-dot"></div>
      <div class="brand-name"><span class="line1">HALDEN</span><span class="line2">REALTY</span></div>
    </div>
  </section>

  <section class="card card-back" aria-label="Card back">
    <div class="ghost-ring"></div>
    <div class="brand">
      <div class="brand-dot"></div>
      <div class="brand-name"><span class="line1">HALDEN</span><span class="line2">REALTY</span></div>
    </div>
    <div class="agent">
      <p class="agent-name">MARCUS HALE</p>
      <p class="agent-title">Managing Director</p>
      <ul class="contact-list">
        <li><svg viewBox="0 0 16 16" fill="none" stroke="#f2f2f2" stroke-width="1.6"><path d="M4 1.5l2.5 3-1.5 1.5c.8 2 2.5 3.7 4.5 4.5L11 9l3 2.5-1.5 2.5C7 14 2 9 2 3.5z"/></svg>044-555 018 274</li>
        <li><svg viewBox="0 0 16 16" fill="none" stroke="#f2f2f2" stroke-width="1.6"><rect x="1.5" y="3.5" width="13" height="9"/><path d="M1.5 3.5L8 9l6.5-5.5"/></svg>info@haldenrealty.example</li>
        <li><svg viewBox="0 0 16 16" fill="none" stroke="#f2f2f2" stroke-width="1.4"><circle cx="8" cy="8" r="6.5"/><ellipse cx="8" cy="8" rx="2.8" ry="6.5"/><path d="M1.5 8h13"/></svg>www.haldenrealty.example</li>
      </ul>
      <p class="address">421, Address line goes here<br>45452, Country Name</p>
    </div>
  </section>
</body>
</html>
```